Kestrel Facilities Business Card Design

We would now like to design business cards with the new Kestrel Facilities logo

Target Market(s)

Professional

Industry/Entity Type

Professional services

Contact Information for Business Card

Employee name, title, phone number, email address, corporate office address and logo.

Font styles to use
Sans Serif

Colors
0054AA
0677BA
7BADD7
CADEEF
E8F1F8

Requirements
Must have
• My logo
Should not have
• any other pictures or images besides my logo

```html
<!DOCTYPE html>
<html lang="en">
<head>
<meta charset="utf-8">
<title>Kestrel Facilities Business Card</title>
<link href="https://fonts.googleapis.com/css2?family=Montserrat:wght@400;500;700&display=swap" rel="stylesheet">
<style>
  :root {
    --brand-blue: #3478c1;
    --deep-blue: #0054aa;
    --paper: #ffffff;
    --ink: #1c1c1c;
    --backdrop: #d9dadc;
    --light-tint: #e8f1f8;
  }
  * { box-sizing: border-box; margin: 0; padding: 0; }
  html, body {
    width: 1200px; height: 813px; overflow: hidden;
    background: var(--backdrop);
    font-family: "Montserrat", Arial, sans-serif;
  }
  .stage {
    width: 1200px; height: 813px;
    display: flex; align-items: center; justify-content: center; gap: 40px;
  }
  .card {
    position: relative;
    width: 540px; height: 310px;
    border-radius: 22px;
    overflow: hidden;
    box-shadow: 0 6px 18px rgba(0,0,0,0.18);
  }
  .card-front { background: var(--paper); }
  .card-back { background: var(--brand-blue); display: flex; align-items: center; justify-content: center; }

  .brand {
    display: flex; align-items: center; gap: 12px;
    color: var(--brand-blue);
    font-weight: 700;
    text-transform: uppercase;
    line-height: 1.05;
  }
  .brand-square { width: 40px; height: 40px; border: 5px solid currentColor; flex: none; }
  .card-front .brand { position: absolute; left: 34px; top: 118px; font-size: 23px; }
  .card-back .brand { color: var(--light-tint); font-size: 44px; gap: 20px; }
  .card-back .brand-square { width: 70px; height: 70px; border-width: 8px; }

  .divider {
    position: absolute; left: 258px; top: 72px;
    width: 2px; height: 150px; background: var(--brand-blue);
  }
  .details { position: absolute; left: 282px; top: 40px; color: var(--ink); font-size: 14px; line-height: 1.35; }
  .person-name { color: var(--brand-blue); font-weight: 700; font-size: 19px; letter-spacing: 0.3px; }
  .person-title { font-size: 15px; margin-bottom: 14px; }
  .address { margin-bottom: 14px; }
  .contact-line { display: flex; align-items: center; gap: 8px; }
  .contact-line svg { width: 15px; height: 15px; flex: none; fill: var(--brand-blue); }

  .web-band {
    position: absolute; right: 0; bottom: 0;
    width: 320px; height: 44px;
    background: var(--brand-blue);
    clip-path: polygon(8px 0, 100% 0, 100% 100%, 0 100%);
    display: flex; align-items: center; justify-content: flex-end;
    padding-right: 70px;
    color: var(--paper); font-size: 14px; letter-spacing: 0.3px;
  }
</style>
</head>
<body>
<main class="stage">
  <section class="card card-front">
    <div class="brand"><span class="brand-square"></span><span>Kestrel<br>Facilities</span></div>
    <div class="divider"></div>
    <div class="details">
      <p class="person-name">DARREN HOLLOWAY</p>
      <p class="person-title">Co-Founder</p>
      <p class="address">4180 N. Harbor Avenue<br>Suite 210 Lakeview 42</p>
      <p class="contact-line">
        <svg viewBox="0 0 24 24" aria-hidden="true"><path d="M6.6 10.8a15 15 0 0 0 6.6 6.6l2.2-2.2a1 1 0 0 1 1-.25 11.4 11.4 0 0 0 3.6.57 1 1 0 0 1 1 1V20a1 1 0 0 1-1 1A17 17 0 0 1 3 4a1 1 0 0 1 1-1h3.5a1 1 0 0 1 1 1c0 1.25.2 2.45.57 3.57a1 1 0 0 1-.25 1z"/></svg>
        +254-700-31452
      </p>
      <p class="contact-line">
        <svg viewBox="0 0 24 24" aria-hidden="true"><path d="M2 5h20v14H2z M4 7v.4l8 5.3 8-5.3V7l-8 5.3z" fill-rule="evenodd"/></svg>
        hello@kestrelfm.com
      </p>
    </div>
    <div class="web-band">www.kestrelfm.com</div>
  </section>

  <section class="card card-back">
    <div class="brand"><span class="brand-square"></span><span>Kestrel<br>Facilities</span></div>
  </section>
</main>
</body>
</html>
```